Business Card for Vorla Parts Wholesale supplier

Hi There! I need a new business card for our company. We are specialized in selling Vorla parts, mostly we sell new LCD screens for Zelnar and Drelks. I would like to see that back in the design.

You can find the colors and logo's on our website: www.hartuvo.nl

Industry/Entity Type

Business

Contact Information for Business Card

My Details:
Tobias Lindqvist

Phone: 0031687203316
E-mail: Tobias@hartuvo.nl

Slogan: "Because Quality Matters"

Font styles to use
Sans Serif

Colors

Designer to choose colors to be used in the design.

Requirements
Must have
• A Black backside with the Hartuvo logo on it. The front side should be clean with only my contact details.
• But I'm also open for something really different or awesome!
Nice to have
• Remember that we are in the parts & repairing industry, So i'll be handing those business cards mainly to repair companies. Maybe you can do something with that thought :)

```html
<!DOCTYPE html>
<html lang="en">
<head>
<meta charset="utf-8">
<title>Hartuvo Business Card</title>
<link rel="stylesheet" href="https://fonts.googleapis.com/css2?family=Open+Sans:wght@400;700;800&display=swap">
<style>
  :root {
    --backdrop: #2b2b2d;
    --card: #1d1e21;
    --card-shade: #232427;
    --orange: #f07c22;
    --white: #ffffff;
    --text-soft: #f1f1f1;
  }
  * { margin: 0; padding: 0; box-sizing: border-box; }
  html, body {
    width: 1200px;
    height: 1189px;
    overflow: hidden;
    background: var(--backdrop);
    font-family: "Open Sans", Arial, sans-serif;
  }
  .canvas {
    position: relative;
    width: 1200px;
    height: 1189px;
  }
  .card {
    position: absolute;
    left: 180px;
    width: 840px;
    height: 494px;
    border-radius: 34px;
    background: linear-gradient(135deg, var(--card) 0%, var(--card-shade) 100%);
    box-shadow: 0 18px 40px rgba(0, 0, 0, 0.45);
    overflow: hidden;
  }
  .card--back { top: 60px; }
  .card--front { top: 630px; }

  .brand {
    display: flex;
    align-items: center;
    gap: 22px;
  }
  .brand__dot {
    width: 74px;
    height: 74px;
    border-radius: 50%;
    background: var(--orange);
    flex: none;
  }
  .brand__name {
    color: var(--white);
    font-weight: 800;
    font-size: 92px;
    line-height: 1;
    letter-spacing: 1px;
  }

  .card--back .brand {
    position: absolute;
    left: 50%;
    top: 50%;
    transform: translate(-50%, -50%);
  }

  .card--front .brand {
    position: absolute;
    left: 60px;
    top: 62px;
  }
  .card--front .brand__dot { width: 62px; height: 62px; }
  .card--front .brand__name { font-size: 80px; }

  .contact {
    position: absolute;
    left: 86px;
    top: 232px;
    color: var(--text-soft);
  }
  .contact__name {
    color: var(--orange);
    font-weight: 700;
    font-size: 34px;
    margin-bottom: 26px;
  }
  .contact__line {
    font-size: 25px;
    line-height: 1.32;
  }
  .contact__label {
    color: var(--orange);
    font-weight: 700;
  }
  .contact__accent { color: var(--orange); }
  .slogan {
    margin-top: 24px;
    color: var(--white);
    font-weight: 700;
    font-size: 27px;
    letter-spacing: 0.3px;
  }
</style>
</head>
<body>
<main class="canvas">
  <section class="card card--back" aria-label="Card back">
    <div class="brand">
      <span class="brand__dot"></span>
      <span class="brand__name">hartuvo</span>
    </div>
  </section>

  <section class="card card--front" aria-label="Card front">
    <div class="brand">
      <span class="brand__dot"></span>
      <span class="brand__name">hartuvo</span>
    </div>
    <div class="contact">
      <p class="contact__name">Tobias Lindqvist</p>
      <p class="contact__line"><span class="contact__label">P:</span> 0031687203316</p>
      <p class="contact__line"><span class="contact__label">E:</span> Tobias@hartuvo.nl</p>
      <p class="contact__line">www.<span class="contact__accent">hartuvo</span>.nl</p>
      <p class="slogan">Because Quality Matters</p>
    </div>
  </section>
</main>
</body>
</html>
```